Business Card for beauty technology startup

Design Glimora Business Card for a Beauty, based on the website identity and colors (https://www.glimora-example.com).
Glimora is a beauty tech startup that gathers helpful product info for beauty lovers and consumers (such as availability on stores, price range and product reviews) for makeup products. The card design must be young, colorful but clean, and very modern.

Target Market(s)

woman, 15-35

Industry/Entity Type

Cosmetics

Contact Information for Business Card

Full Name, address, phone

Font styles to use
Other font styles liked:
• Advent Pro

Colors
e34297
86cfc6
ffffff
5c5c5c
e8e8e8
e667a6
b2b2b2

Requirements
Must have
• One full colored side with a creative design and another with card info
• Use Color palette: #95C5C5 and/or #D38AA5
• Use fonts: Advent Pro
• Use website identity: https://www.glimora-example.com
Nice to have
• If needed extra font: Roboto

```html
<!DOCTYPE html>
<html lang="en">
<head>
<meta charset="utf-8">
<title>Glimora Business Card</title>
<link href="https://fonts.googleapis.com/css2?family=Advent+Pro:wght@300;400&family=Roboto:wght@400;500&display=swap" rel="stylesheet">
<style>
  :root {
    --bg: #2b2b2b;
    --paper: #f4f4f4;
    --rose: #b98094;
    --grey-band: #a9a9a9;
    --ink: #4a4a4a;
    --white: #ffffff;
  }
  * { margin: 0; padding: 0; box-sizing: border-box; }
  html, body { width: 1200px; height: 960px; overflow: hidden; }
  body { background: var(--bg); position: relative; font-family: "Roboto", Arial, sans-serif; }

  .card {
    position: absolute;
    width: 600px;
    height: 343px;
    border-radius: 22px;
    overflow: hidden;
  }
  .card-front { left: 314px; top: 113px; background: var(--paper); }
  .card-back  { left: 311px; top: 472px; background: var(--rose); }

  .name-band {
    position: absolute; left: 0; top: 39px; width: 100%; height: 86px;
    background: var(--rose);
  }
  .name-band-accent {
    position: absolute; right: 0; top: 0; width: 78px; height: 100%;
    background: var(--grey-band);
  }
  .band-disc {
    position: absolute; left: 445px; top: -2px; width: 92px; height: 90px;
  }
  .holder-name {
    position: absolute; left: 33px; top: 22px;
    color: var(--white); font-weight: 500; font-size: 21px; line-height: 1;
  }
  .holder-title {
    position: absolute; left: 33px; top: 50px;
    color: var(--white); font-size: 14px; line-height: 1;
  }
  .brand-name {
    position: absolute; right: 33px; top: 146px;
    color: var(--rose); font-family: "Advent Pro", "Roboto", sans-serif;
    font-weight: 300; font-size: 40px; letter-spacing: 5px; line-height: 1;
  }
  .contact-list {
    position: absolute; left: 35px; top: 253px; list-style: none;
    color: var(--ink); font-size: 14px; line-height: 19.5px;
  }
  .contact-list li { display: flex; align-items: center; gap: 8px; }
  .contact-list svg { width: 13px; height: 13px; fill: var(--rose); }
  .address {
    position: absolute; right: 33px; top: 253px; text-align: right;
    color: var(--ink); font-size: 14px; line-height: 19.5px; font-style: normal;
  }
  .address .web { color: var(--rose); letter-spacing: 0.5px; }

  .back-brand {
    position: absolute; left: 0; top: 130px; width: 100%;
    display: flex; justify-content: center; align-items: center; gap: 18px;
  }
  .back-brand .dot {
    width: 22px; height: 22px; border-radius: 50%; background: var(--white);
  }
  .back-brand .word {
    color: var(--white); font-family: "Advent Pro", "Roboto", sans-serif;
    font-weight: 400; font-size: 62px; letter-spacing: 6px; line-height: 1;
  }
  .back-web {
    position: absolute; left: 0; top: 296px; width: 100%; text-align: center;
    color: var(--white); font-size: 14px; letter-spacing: 5px;
  }
</style>
</head>
<body>
  <section class="card card-front">
    <div class="name-band">
      <div class="name-band-accent"></div>
      <svg class="band-disc" viewBox="0 0 92 90" aria-hidden="true">
        <circle cx="46" cy="45" r="44" fill="var(--white)"/>
      </svg>
      <div class="holder-name">MARA ELLISON</div>
      <div class="holder-title">CEO/FOUNDER</div>
    </div>
    <div class="brand-name">GLIMORA</div>
    <ul class="contact-list">
      <li><svg viewBox="0 0 16 16"><path d="M3 1l3 3-1.5 2a9 9 0 0 0 5.5 5.5L12 10l3 3-2 2C7 15 1 9 1 3z"/></svg>555 214 7730</li>
      <li><svg viewBox="0 0 16 16"><path d="M4 0h8v16H4zM5.5 2v10h5V2z"/></svg>555 382 6491</li>
      <li><svg viewBox="0 0 16 16"><path d="M1 3h14v10H1zM2 4l6 5 6-5z"/></svg>info@glimora-example.com</li>
    </ul>
    <address class="address">
      2140 Larkspur Way<br>
      Juneau, Alaska 99801<br>
      <span class="web">www.glimora-example.com</span>
    </address>
  </section>

  <section class="card card-back">
    <div class="back-brand">
      <span class="dot"></span>
      <span class="word">Glimora</span>
    </div>
    <div class="back-web">www.glimora-example.com</div>
  </section>
</body>
</html>
```